BrightLedgerMoney(.com) needs website & logo design

We need our website mock-up made into a reality! We are wanting to launch a multifaceted website for all things financial - i.e. blogs, financial wellness information, and a network of redirect links.
We have an existing mock-up, which I will include, but are open to your creative approach!

Industry/Entity Type

Finance

Coding

Coded - Design and coding required

Number of Pages Required

1 page

Requirements
Must have
• Corresponding logo

```html
<!DOCTYPE html>
<html lang="en">
<head>
<meta charset="utf-8">
<title>Bright Ledger Money</title>
<link rel="stylesheet" href="https://fonts.googleapis.com/css2?family=Libre+Franklin:wght@400;500;600;700;800&display=swap">
<style>
:root{
  --navy:#123a5c;
  --navy-deep:#0b2640;
  --teal:#72d6c1;
  --purple:#a58ac9;
  --purple-strong:#9a7cc3;
  --ink:#2a2a2a;
  --body:#555;
  --white:#fff;
  --black:#000;
}
*{margin:0;padding:0;box-sizing:border-box}
html,body{width:1200px;height:3439px;overflow:hidden;background:var(--white)}
body{position:relative;font-family:"Libre Franklin",Arial,sans-serif;color:var(--ink)}
.abs{position:absolute}
.btn{position:absolute;display:flex;align-items:center;justify-content:center;color:var(--white);font-weight:600;font-size:14px;text-decoration:none}
.btn-teal{background:var(--teal)}
.btn-purple{background:var(--purple-strong)}

/* hero */
.hero{left:0;top:0;width:1200px;height:660px;background:linear-gradient(135deg,#1b4f7a 0,#174569 45%,#123a5c 100%)}
.hero-visual{left:700px;top:0;width:500px;height:660px;background:
  radial-gradient(ellipse 130px 160px at 205px 395px,rgba(90,150,255,.95) 0,rgba(40,90,230,.75) 45%,rgba(30,70,160,0) 100%),
  radial-gradient(ellipse 40px 90px at 205px 120px,#3a2a26 0,#2a201d 70%,rgba(40,30,28,0) 100%),
  radial-gradient(circle at 60% 50%,rgba(40,110,180,.35),rgba(18,58,92,0) 70%)}
.site-header{left:0;top:0;width:1200px;height:85px;background:rgba(8,26,44,.82);border-radius:0 0 26px 26px}
.brand{left:112px;top:25px;font-size:30px;font-weight:800;color:var(--white);letter-spacing:.3px}
.menu-icon{left:1054px;top:32px}
.hero-title{left:112px;top:172px;font-size:64px;line-height:78px;font-weight:800;color:var(--white)}
.hero-text{left:112px;top:426px;font-size:14px;line-height:28px;font-weight:500;color:var(--white)}

/* signup */
.signup-band{left:0;top:660px;width:1200px;height:82px;background:var(--purple)}
.signup-box{left:110px;top:740px;width:978px;height:91px;background:var(--purple);border-radius:0 0 46px 46px}
.signup-title{left:0;top:682px;width:1200px;text-align:center;font-size:42px;font-weight:800;color:var(--white)}
.email-field{left:271px;top:753px;width:453px;height:47px;background:var(--white);font-size:12px;color:#444;padding:0 25px;display:flex;align-items:center}

/* trending */
.trend-media{left:111px;top:946px;width:466px;height:473px;background:
  radial-gradient(circle at 65% 35%,#2b8ad0 0,#15568f 40%,#0b2a4c 80%);border-radius:0 70px 0 70px}
.trend-title{left:639px;top:990px;font-size:42px;line-height:56px;font-weight:800;color:var(--ink)}
.trend-text{left:639px;top:1116px;width:405px;font-size:12.5px;line-height:25.8px;color:var(--body)}

/* steps */
.steps{left:110px;top:1500px}
.step-label{position:absolute;top:1655px;width:140px;text-align:center;font-size:15px;line-height:21px;color:#555}

/* tools */
.tools-band{left:0;top:1786px;width:1200px;height:303px;background:linear-gradient(180deg,#a98ccb,#9f86c4)}
.tool-card{position:absolute;top:1864px;width:152px;height:148px;background:var(--white);border-radius:3px;box-shadow:0 2px 6px rgba(0,0,0,.12)}
.tool-art{position:absolute;left:36px;top:18px;width:80px;height:80px;border-radius:50%}
.tool-name{position:absolute;left:0;top:118px;width:100%;text-align:center;font-size:15px;color:#333}

/* blog */
.blog-heading{left:0;top:2150px;width:1200px;text-align:center;font-size:42px;font-weight:800;color:var(--ink)}
.post{position:absolute;top:2233px;width:315px}
.post-media{width:315px;height:186px}
.post-title{margin:28px 15px 0;font-size:23px;line-height:32px;font-weight:600;color:#333}
.post-text{margin:12px 15px 0;font-size:12px;line-height:25px;color:#555}
.read-more{display:inline-block;margin:10px 15px 0;font-size:12px;font-weight:700;color:var(--purple-strong);text-decoration:underline}

/* cta */
.footer-bg{left:0;top:2974px;width:1200px;height:465px;background:var(--black)}
.cta{top:2825px;height:293px;width:489px}
.cta-left{left:111px;background:linear-gradient(135deg,#6fd8c2,#62d0b8);border-radius:6px 0 0 6px}
.cta-right{left:599px;width:489px;background:linear-gradient(135deg,#9c84c4,#8e76b9);border-radius:0 6px 6px 0}
.cta-title{position:absolute;left:0;width:100%;text-align:center;font-size:28px;font-weight:800;color:var(--white)}
.cta-text{position:absolute;left:40px;width:409px;text-align:center;font-size:12px;line-height:21.5px;color:var(--white)}

/* footer */
.footer-brand{left:0;top:3192px;width:1200px;text-align:center;font-size:38px;font-weight:800;color:var(--white)}
.footer-nav{left:0;top:3280px;width:1200px;display:flex;justify-content:center;gap:48px;font-size:14px;font-weight:600;color:var(--white)}
.social{left:0;top:3330px;width:1200px;display:flex;justify-content:center;gap:15px}
.social span{width:35px;height:35px;border-radius:50%;background:var(--white)}
.copyright{left:0;top:3386px;width:1200px;text-align:center;font-size:13px;font-weight:500;color:var(--white)}
</style>
</head>
<body>

<section class="abs hero"></section>
<div class="abs hero-visual" role="img" aria-label="Hanging light bulb with a glowing blue digital wireframe bulb"></div>
<header class="abs site-header"></header>
<div class="abs brand">BRIGHT LEDGER MONEY</div>
<svg class="abs menu-icon" width="30" height="22" viewBox="0 0 30 22" aria-label="Menu">
  <g fill="#fff"><rect x="0" y="0" width="5" height="4"/><rect x="8" y="0" width="22" height="4"/><rect x="0" y="9" width="5" height="4"/><rect x="8" y="9" width="22" height="4"/><rect x="0" y="18" width="5" height="4"/><rect x="8" y="18" width="22" height="4"/></g>
</svg>
<h1 class="abs hero-title">A CLEAR PATH<br>TO FINANCIAL<br>WELLNESS</h1>
<p class="abs hero-text">Having insight tp relevant information is what we bring to you<br>in a clear and easy to digest way.</p>
<a class="btn btn-teal" style="left:112px;top:505px;width:148px;height:46px">Get Started</a>

<div class="abs signup-band"></div>
<div class="abs signup-box"></div>
<h2 class="abs signup-title">SIGNUP FOR FREE</h2>
<div class="abs email-field">Your Email Address</div>
<a class="btn btn-teal" style="left:742px;top:753px;width:187px;height:47px">Get Started</a>

<div class="abs trend-media" role="img" aria-label="Hand touching a glowing 2022 financial growth chart"></div>
<h2 class="abs trend-title">TRENDING IN 2021:<br>FINANCIAL LITERACY</h2>
<p class="abs trend-text">There are many variations of passages of Lorem Ipsum available, but the majority have suffered alteration in some form, by injected humour, or randomised words which don't look even slightly believable. If you are going to use a passage of Lorem Ipsum, you need to be sure there predefined chunks as necessary, making this the first true generator on the Internet. It uses a dictionary of over 200 Latin words, combined with a handful of model sentence structures, to generate Lorem Ipsum which looks reasonable. The generated Lorem Ipsum is therefore always free from repetition, injected humour, or non-characteristic words etc.</p>

<svg class="abs steps" width="980" height="150" viewBox="0 0 980 150">
  <g fill="none" stroke-width="13" stroke-linecap="round">
    <path d="M150 95 C185 150 230 140 250 100" stroke="#72d6c1"/>
    <path d="M290 55 C320 10 360 10 380 55" stroke="#a58ac9"/>
    <path d="M455 100 C480 150 525 140 540 100" stroke="#72d6c1"/>
    <path d="M590 55 C620 10 660 10 680 55" stroke="#a58ac9"/>
    <path d="M755 100 C780 150 820 140 838 100" stroke="#72d6c1"/>
    <circle cx="112" cy="77" r="52" stroke="#72d6c1"/>
    <circle cx="269" cy="77" r="46" stroke="#a58ac9" stroke-dasharray="200 90"/>
    <circle cx="420" cy="77" r="46" stroke="#72d6c1" stroke-dasharray="200 90"/>
    <circle cx="568" cy="77" r="46" stroke="#a58ac9" stroke-dasharray="200 90"/>
    <circle cx="718" cy="77" r="46" stroke="#72d6c1" stroke-dasharray="200 90"/>
    <circle cx="869" cy="77" r="52" stroke="#72d6c1"/>
  </g>
  <g>
    <circle cx="112" cy="77" r="40" fill="#72d6c1"/>
    <circle cx="269" cy="77" r="40" fill="#a58ac9"/>
    <circle cx="420" cy="77" r="40" fill="#72d6c1"/>
    <circle cx="568" cy="77" r="40" fill="#a58ac9"/>
    <circle cx="718" cy="77" r="40" fill="#72d6c1"/>
    <circle cx="869" cy="77" r="40" fill="#a58ac9"/>
  </g>
  <g fill="none" stroke="#fff" stroke-width="2.5">
    <circle cx="112" cy="77" r="20"/><circle cx="112" cy="77" r="12"/><circle cx="112" cy="77" r="4"/>
    <rect x="404" y="66" width="32" height="22" rx="3"/><path d="M412 66 l4 -10 h8 l4 10"/>
    <rect x="552" y="64" width="32" height="24" rx="3"/><path d="M552 72 h32"/>
    <circle cx="714" cy="75" r="15"/><path d="M714 60 v15 h15"/>
    <circle cx="869" cy="70" r="8"/><path d="M850 92 h16 l12 -8"/>
  </g>
  <text x="269" y="91" text-anchor="middle" fill="#fff" font-family="Libre Franklin, sans-serif" font-weight="800" font-size="40">$</text>
  <text x="420" y="84" text-anchor="middle" fill="#fff" font-family="Libre Franklin, sans-serif" font-weight="700" font-size="16">$</text>
</svg>
<div class="step-label" style="left:156px">Set Goals</div>
<div class="step-label" style="left:309px">Money 101</div>
<div class="step-label" style="left:460px">Budgeting</div>
<div class="step-label" style="left:608px">Credit<br>Mindfulness</div>
<div class="step-label" style="left:758px">Debt<br>Management</div>
<div class="step-label" style="left:909px">Retirement<br>Planning</div>

<section class="abs tools-band"></section>
<div class="tool-card" style="left:99px"><div class="tool-art" role="img" aria-label="Money bag in hand illustration" style="background:radial-gradient(circle at 50% 40%,#f4c46a,#e9a64b 60%,#fff 72%)"></div><div class="tool-name">Save</div></div>
<div class="tool-card" style="left:268px"><div class="tool-art" role="img" aria-label="Red money bag and coin stacks illustration" style="background:radial-gradient(circle at 50% 45%,#ef5a5a,#f6c23e 60%,#fff 72%)"></div><div class="tool-name">Budget</div></div>
<div class="tool-card" style="left:438px"><div class="tool-art" role="img" aria-label="Calculator and receipt illustration" style="background:radial-gradient(circle at 50% 45%,#7ed3a4,#f0c55b 60%,#fff 72%)"></div><div class="tool-name">Calculate</div></div>
<div class="tool-card" style="left:608px"><div class="tool-art" role="img" aria-label="Route with location pin illustration" style="background:radial-gradient(circle at 50% 45%,#5cc7d6,#f1b84a 60%,#fff 72%)"></div><div class="tool-name">Track</div></div>
<div class="tool-card" style="left:778px"><div class="tool-art" role="img" aria-label="Magnifier over bar chart illustration" style="background:radial-gradient(circle at 50% 45%,#6ab3e6,#e8687b 60%,#fff 72%)"></div><div class="tool-name">Research</div></div>
<div class="tool-card" style="left:948px"><div class="tool-art" role="img" aria-label="Money bag with rising bars illustration" style="background:radial-gradient(circle at 50% 45%,#4cbf7a,#f5c04a 60%,#fff 72%)"></div><div class="tool-name">Invest</div></div>

<h2 class="abs blog-heading">LATEST BLOG</h2>
<article class="post" style="left:111px">
  <div class="post-media" role="img" aria-label="Professional at an office desk" style="background:linear-gradient(90deg,#e6e8ec 0,#cfd3da 40%,#2f3647 100%)"></div>
  <h3 class="post-title">There are many variations of passages</h3>
  <p class="post-text">There are many variations of passages of Lorem Ipsum available, but the majority have suffered alteration in some form, by injected humour, or randomised words which</p>
  <a class="read-more">Read More</a>
</article>
<article class="post" style="left:442px">
  <div class="post-media" role="img" aria-label="Rising coin stacks with a target on top" style="background:linear-gradient(180deg,#bfe0ee 0,#cfe6ef 55%,#d9c9a6 100%)"></div>
  <h3 class="post-title">There are many variations of passages</h3>
  <p class="post-text">There are many variations of passages of Lorem Ipsum available, but the majority have suffered alteration in some form, by injected humour, or randomised words which</p>
  <a class="read-more">Read More</a>
</article>
<article class="post" style="left:773px">
  <div class="post-media" role="img" aria-label="Traveller with passport and piggy bank" style="background:linear-gradient(90deg,#d9d9d7 0,#cfcfcc 40%,#b8675a 100%)"></div>
  <h3 class="post-title">There are many variations of passages</h3>
  <p class="post-text">There are many variations of passages of Lorem Ipsum available, but the majority have suffered alteration in some form, by injected humour, or randomised words which</p>
  <a class="read-more">Read More</a>
</article>
<a class="btn btn-teal" style="left:526px;top:2699px;width:148px;height:47px">View More</a>

<footer class="abs footer-bg"></footer>
<section class="abs cta cta-left">
  <h3 class="cta-title" style="top:68px">HAVE ANY QUESTIONS?</h3>
  <p class="cta-text" style="top:114px">There are many variations of passages of Lorem Ipsum available, but the majority have suffered alteration in some form, by injected humour, or randomised words which don't look even</p>
  <a class="btn btn-purple" style="left:171px;top:183px;width:148px;height:46px">Get Started</a>
</section>
<section class="abs cta cta-right">
  <h3 class="cta-title" style="top:60px">FINANCIAL WELLNESS 101</h3>
  <p class="cta-text" style="top:107px">There are many variations of passages of Lorem Ipsum available, but the majority have suffered alteration in some form, by injected humour, or randomised words which don't look even</p>
  <a class="btn btn-teal" style="left:171px;top:189px;width:148px;height:47px">Get Started</a>
</section>

<div class="abs footer-brand">BRIGHT LEDGER MONEY</div>
<nav class="abs footer-nav"><span>Home</span><span>|</span><span>About Us</span><span>|</span><span>Services</span><span>|</span><span>Blog</span><span>|</span><span>Contact Us</span></nav>
<div class="abs social" aria-label="Social links"><span></span><span></span><span></span></div>
<p class="abs copyright">© Copyright 2023 Bright Ledger Money | All Rights Reserved.</p>

</body>
</html>
```